Marrowind - IT Consultancy Website

Our company is called Marrowind and our purpose is to help companies sustainably embrace and reap the benefits of cloud platforms, through transforming practices, skills and technology using DevOps and Security practices such that they are able to automate, manage and secure their cloud platforms to deliver product to market with increasing velocity.

To get our business started I require a website that will model the typical layout of an IT consultancy services company to an Australian Market. There are many examples of such a site, here are some of them. We would like a landing page and then a few simple menu options (About, Blog, Services etc..) to additional content

http://pelvo.com.au/
http://www.brisket.com.au/
http://www.tandu.com.au/

I require the site to be created with a separate CSS file that maintains the colour palette. This is a very important requirement, I want to be able to change the colours employed in the site in a single location and not have to scan through multiple files to replace the codes.

The website must be built using static content as it will not be hosted on a web server but instead in QNT using S3 and CloudFront CDN. Therefore please stick to HTML, JavaScript, CSS and other static file formats. The website needs to be response, smooth and reactive. It should render on desktop, mobile and tablet and feature smooth scrolling, transitions and fade in's.

The website should give the customer confidence that they are dealing with a highly professional IT services company, focused strongly on cloud (QNT, Vantrel Skyline, Horvik Vapor etc..), motivated by beautiful and fluid design.

In order to make this simpler for you, the designer, I have already purchased this template from https://skinmarketly.com/theme/the-venture-allround-template-KX7Q41093 and uploaded it. Feel free to use this template if you choose (note that it makes use of a separate color palette which is a key requirement) or use one of your own choosing. If you do use this template ensure that it does not look too much like "another bootstrap site" therefore use the layout and widgets but make the site look fresh and original too.
Obviously you must delete all trace of the bootstrap package once the project has completed if you do use it

Target Market(s)

Corporate and medium enterprise businesses

Industry/Entity Type

Information Technology

Coding

Coded - Design and coding required

Number of Pages Required

4 page

Font styles to use
Sans Serif

Colors
abd036
33a6d7

Requirements
Must have
• The website should give the customer confidence that they are dealing with a highly professional IT services company, focused strongly on cloud (QNT, Vantrel Skyline, Horvik Vapor etc..), motivated by beautiful and fluid design. Our company name is Marrowind, the site needs to pay homage to the themes of fluidity and logic
• Along with About Us, Services and a Blog page could I also get social logo's included too
Nice to have
• The website must be built using static content as it will not be hosted on a web server but instead in QNT using S3 and CloudFront CDN. Therefore please stick to HTML, JavaScript, CSS and other static file formats. The website needs to be response, smooth and reactive. It should render on desktop, mobile and tablet and feature smooth scrolling, transitions and fade in's.
Should not have
• Lurid colours, or too much animations. The design must "flow"

```html
<!DOCTYPE html>
<html lang="en">
<head>
<meta charset="utf-8">
<title>Marrowind IT Consultancy</title>
<link rel="stylesheet" href="https://fonts.googleapis.com/css2?family=Open+Sans:wght@400;600;700&display=swap">
<style>
:root{
  --brand:#1d3f8f;
  --accent:#1aa0f0;
  --accent-dark:#0a7fd8;
  --ink:#2b2b2b;
  --muted:#6b6b6b;
  --page:#ffffff;
  --soft:#f4f4f4;
  --line:#dddddd;
  --hero-a:#1c232c;
  --hero-b:#4a5868;
  --dark:#3a3a3a;
  --footer-bar:#e6e6e6;
}
*{box-sizing:border-box;margin:0;padding:0}
html,body{width:1200px;height:3046px;overflow:hidden}
body{font-family:"Open Sans",Arial,sans-serif;color:var(--ink);background:var(--page);position:relative}
section,header,footer{position:absolute;left:0;width:1200px}
.btn{display:inline-block;background:var(--accent);color:#fff;font-weight:600;text-transform:uppercase;border-radius:6px;text-align:center}

/* header */
.site-header{top:0;height:92px;background:linear-gradient(#f7f7f7,#e7e7e7)}
.brand{position:absolute;left:172px;top:24px;text-align:center}
.brand-name{font-size:21px;font-weight:700;color:var(--brand);letter-spacing:.5px;line-height:1}
.brand-sub{font-size:10px;letter-spacing:3px;color:var(--muted);margin-top:5px}
.main-nav{position:absolute;left:516px;top:34px;display:flex;gap:0}
.main-nav a{font-size:14px;color:var(--ink);text-decoration:none;margin-right:48px;position:relative;padding-bottom:16px}
.main-nav a.active:after{content:"";position:absolute;left:-6px;right:-6px;bottom:0;height:3px;background:var(--brand)}

/* hero */
.hero{top:92px;height:492px}
.hero-photo{position:absolute;inset:0;background:radial-gradient(ellipse at 40% 40%,var(--hero-b),var(--hero-a) 75%)}
.hero-title{position:absolute;top:218px;width:100%;text-align:center;color:#fff;font-size:28px;line-height:37px}
.hero .btn{position:absolute;left:497px;top:313px;width:205px;height:47px;line-height:47px;border-radius:24px;font-size:13px;background:var(--accent-dark)}
.dots{position:absolute;top:448px;left:568px;display:flex;gap:8px}
.dots i{width:9px;height:9px;border-radius:50%;background:#fff;opacity:.6}
.dots i:first-child{opacity:1;background:var(--accent)}

/* pillars */
.pillars{top:584px;height:248px;background:var(--soft)}
.pillar{position:absolute;top:42px;width:260px}
.pillar h3{display:flex;align-items:center;gap:10px;font-size:23px;font-weight:400;color:var(--ink)}
.pillar p{margin:20px 0 0 44px;font-size:11px;line-height:19px;color:var(--muted)}
.pillar .btn{margin:14px 0 0 44px;font-size:10px;text-transform:none;padding:4px 12px;border-radius:10px}

/* why */
.why{top:832px;height:508px}
.why h2{position:absolute;left:174px;top:52px;font-size:23px;font-weight:600}
.accordion{position:absolute;left:174px;top:120px;width:416px}
.acc{border:1px solid var(--line);border-radius:4px;margin-bottom:14px;display:flex;align-items:center;height:40px;padding:0 14px;font-size:13px;position:relative}
.acc.open{height:156px;background:var(--soft);display:block;padding:18px 14px}
.acc .mark{width:12px;height:12px;border:2px solid var(--accent);border-radius:2px;margin-right:16px;flex:none;display:inline-block;vertical-align:middle}
.acc.open strong{font-size:13px;font-weight:600}
.acc.open p{margin:14px 0 0 30px;font-size:11px;line-height:19px;color:var(--muted)}
.acc .plus{position:absolute;right:10px;bottom:12px;width:14px;height:14px;background:#777;border-radius:2px}
.acc:not(.open) .plus{top:13px}
.video{position:absolute;left:610px;top:120px;width:415px;height:298px;border-radius:6px;background:radial-gradient(circle at 60% 50%,#2a5c9c,#0d1f3c 70%)}

/* projects */
.projects{top:1340px;height:625px;background:linear-gradient(#f3f3f3,#eaeaea)}
.projects h2{position:absolute;top:50px;width:100%;text-align:center;color:var(--accent);font-size:26px;font-weight:600}
.card{position:absolute;top:130px;width:269px;height:428px;background:#fff;box-shadow:0 6px 14px rgba(0,0,0,.12);text-align:center}
.card .thumb{height:165px;background:linear-gradient(135deg,#3d5673,#8ba9c8)}
.card h4{margin-top:32px;font-size:13px;color:var(--accent);font-weight:600}
.card p{margin:24px 26px 0;font-size:11px;line-height:20px;color:var(--muted)}
.card .btn{margin-top:16px;width:117px;height:34px;line-height:34px;font-size:10px;border-radius:4px}

/* partners */
.partners{top:1965px;height:207px;display:flex;align-items:center;justify-content:center;gap:80px}
.partner{display:flex;align-items:center;gap:12px;font-size:28px;color:#555}
.partner i{width:36px;height:36px;background:#8a8a8a}

/* testimonial */
.testimonial{top:2172px;height:428px;background:linear-gradient(#4a4a4a,#2e2e2e);color:#fff;text-align:center}
.avatar{position:absolute;left:536px;top:44px;width:128px;height:128px;border-radius:50%;border:4px solid var(--accent);background:#b8a690}
.testimonial h3{position:absolute;top:210px;width:100%;font-size:21px;font-weight:600}
.testimonial hr{position:absolute;top:254px;left:428px;width:344px;border:0;border-top:2px solid #ddd}
.testimonial p{position:absolute;top:276px;left:216px;width:768px;font-size:11px;line-height:20px;color:#e2e2e2}
.arrow{position:absolute;top:202px}

/* footer */
.site-footer{top:2600px;height:446px;background:var(--soft)}
.fcol{position:absolute;top:48px}
.fcol h5{font-size:13px;font-weight:600;text-transform:uppercase}
.fcol p,.fcol li{font-size:11px;line-height:20px;color:#444}
.fcol ul{list-style:none;margin-top:18px}
.fcol li{text-transform:uppercase;font-size:10px;line-height:27px}
.post{display:flex;gap:14px;margin-top:26px}
.post i{width:68px;height:64px;flex:none;background:linear-gradient(135deg,#1b2a44,#4b6b96)}
.gallery{display:grid;grid-template-columns:94px 94px;gap:4px;margin-top:26px}
.gallery i{height:76px;background:linear-gradient(135deg,#2d5b8c,#9bc3e6)}
.social{display:flex;gap:5px;margin:16px 0 22px}
.social i{width:18px;height:18px;border-radius:50%;background:#333}
.contact{display:flex;gap:10px;align-items:center;font-size:11px;line-height:26px;color:#444}
.bottom-bar{position:absolute;left:0;top:390px;width:1200px;height:56px;background:var(--footer-bar);text-align:center;line-height:56px;font-size:10px;font-weight:600}
</style>
</head>
<body>

<header class="site-header">
  <div class="brand"><div class="brand-name">MARROWIND IT</div><div class="brand-sub">CONSULTANCY</div></div>
  <nav class="main-nav">
    <a class="active" href="#">Home</a><a href="#">Features</a><a href="#">Services</a><a href="#">Portfolio</a><a href="#">Blog</a><a href="#">Contact Us</a>
  </nav>
</header>

<section class="hero">
  <div class="hero-photo" role="img" aria-label="Hand holding a cloud shape over a dark technology backdrop"></div>
  <h1 class="hero-title" style="font-weight:400">We are an IT services company<br>focused strongly on cloud</h1>
  <a class="btn">Get Started</a>
  <div class="dots"><i></i><i></i><i></i><i></i></div>
</section>

<section class="pillars">
  <div class="pillar" style="left:180px">
    <h3><svg width="30" height="26" viewBox="0 0 30 26"><rect x="2" y="2" width="26" height="17" rx="2" fill="none" stroke="#1aa0f0" stroke-width="3"/><rect x="10" y="21" width="10" height="3" fill="#1aa0f0"/></svg>Practice</h3>
    <p>Sed ut perspiciatis unde omnis iste natus error sit v rem aperiam, eaque ipsa quae ab illo inventore veritatis et quasi architecto</p>
    <a class="btn">Read More</a>
  </div>
  <div class="pillar" style="left:473px">
    <h3><svg width="30" height="26" viewBox="0 0 30 26"><path d="M9 6 3 13l6 7M21 6l6 7-6 7M17 4l-4 18" fill="none" stroke="#1aa0f0" stroke-width="2.5"/></svg>Skills</h3>
    <p>Sed ut perspiciatis unde omnis iste natus error sit v rem aperiam, eaque ipsa quae ab illo inventore veritatis et quasi architecto</p>
    <a class="btn">Read More</a>
  </div>
  <div class="pillar" style="left:765px">
    <h3><svg width="30" height="26" viewBox="0 0 30 26"><path d="M8 22a6 6 0 0 1 0-12 8 8 0 0 1 15 1 5.5 5.5 0 0 1 0 11z" fill="#1aa0f0"/></svg>Technology</h3>
    <p>Sed ut perspiciatis unde omnis iste natus error sit v rem aperiam, eaque ipsa quae ab illo inventore veritatis et quasi architecto</p>
    <a class="btn">Read More</a>
  </div>
</section>

<section class="why">
  <h2>Why Choose Us ?</h2>
  <div class="accordion">
    <div class="acc open"><span class="mark"></span><strong>Sed ut perspiciatis unde omnis iste natus error sit</strong>
      <p>Sed ut perspiciatis unde omnis iste natus error sit v rem aperiam, eaque ipsa quae ab illo inventore veritatis et quasi architecto. Sed ut perspiciatis unde omnis iste natus error sit voluptatem accusantium</p><span class="plus"></span></div>
    <div class="acc"><span class="mark"></span>Lorem ipsum dolor sit amet, consectetur<span class="plus"></span></div>
    <div class="acc"><span class="mark"></span>Lorem ipsum dolor sit amet, consectetur<span class="plus"></span></div>
    <div class="acc"><span class="mark"></span>Lorem ipsum dolor sit amet, consectetur<span class="plus"></span></div>
  </div>
  <div class="video" role="img" aria-label="Video still of a hand holding a glowing cloud icon">
    <svg width="415" height="298" viewBox="0 0 415 298"><circle cx="207" cy="149" r="36" fill="none" stroke="#fff" stroke-width="4"/><path d="M196 130v38l30-19z" fill="#1aa0f0"/></svg>
  </div>
</section>

<section class="projects">
  <h2>LATEST PROJECTS</h2>
  <div class="card" style="left:174px"><div class="thumb" role="img" aria-label="Hand touching a digital cloud network"></div><h4>CLOUD PLATFORMS</h4><p>Lorem ipsum dolor sit amet, consectetur adipiscing elit, sed do eiusmod tempor incididunt ut labore et dolore magna aliqua. Ut enim ad minim veniam, quis nostrud exercitation ullamco laboris</p><a class="btn">Read More</a></div>
  <div class="card" style="left:466px"><div class="thumb" role="img" aria-label="Tablet showing a cloud above server racks"></div><h4>CLOUD PLATFORMS</h4><p>Lorem ipsum dolor sit amet, consectetur adipiscing elit, sed do eiusmod tempor incididunt ut labore et dolore magna aliqua. Ut enim ad minim veniam, quis nostrud exercitation ullamco laboris</p><a class="btn">Read More</a></div>
  <div class="card" style="left:757px"><div class="thumb" role="img" aria-label="Open hand with a drawn cloud above it"></div><h4>CLOUD PLATFORMS</h4><p>Lorem ipsum dolor sit amet, consectetur adipiscing elit, sed do eiusmod tempor incididunt ut labore et dolore magna aliqua. Ut enim ad minim veniam, quis nostrud exercitation ullamco laboris</p><a class="btn">Read More</a></div>
</section>

<section class="partners">
  <div class="partner"><i></i>QNT</div>
  <div class="partner"><i></i>Vantrel Skyline</div>
  <div class="partner"><i></i>Horvik Vapor</div>
</section>

<section class="testimonial">
  <div class="avatar" role="img" aria-label="Client portrait"></div>
  <svg class="arrow" style="left:68px" width="20" height="28" viewBox="0 0 20 28"><path d="M15 3 5 14l10 11" fill="none" stroke="#fff" stroke-width="3"/></svg>
  <svg class="arrow" style="left:1112px" width="20" height="28" viewBox="0 0 20 28"><path d="M5 3l10 11L5 25" fill="none" stroke="#fff" stroke-width="3"/></svg>
  <h3>Good Experience</h3>
  <hr>
  <p>Sed ut perspiciatis unde omnis iste natus error sit voluptatem accusantium doloremque laudantium, totam rem aperiam, eaque ipsa quae ab illo inventore veritatis et quasi architecto beatae vitae dicta sunt explicabo. Nemo enim ipsam voluptatem quia voluptas sit aspernatur aut odit aut fugit, sed quia consequuntur magni dolores eos qui</p>
</section>

<footer class="site-footer">
  <div class="fcol" style="left:174px;width:180px">
    <div class="brand-name" style="font-size:19px">MARROWIND IT</div><div class="brand-sub" style="margin-bottom:16px">CONSULTANCY</div>
    <p>Lorem ipsum dolor sit amet, consectetur adipiscing elit, sed do eiusmod tempor incididunt.</p>
    <ul><li>Home</li><li>Features</li><li>Services</li><li>Portfolio</li><li>Blog</li><li>Contact Us</li></ul>
  </div>
  <div class="fcol" style="left:394px;width:190px">
    <h5>Latest Blogs</h5>
    <div class="post"><i role="img" aria-label="Blog thumbnail"></i><p>Lorem ipsum dolor sit amet, consectetur adipiscing elit</p></div>
    <div class="post"><i role="img" aria-label="Blog thumbnail"></i><p>Lorem ipsum dolor sit amet, consectetur adipiscing elit</p></div>
    <div class="post"><i role="img" aria-label="Blog thumbnail"></i><p>Lorem ipsum dolor sit amet, consectetur adipiscing elit</p></div>
  </div>
  <div class="fcol" style="left:608px">
    <h5>Photo Gallery</h5>
    <div class="gallery" role="img" aria-label="Gallery of cloud technology photos"><i></i><i></i><i></i><i></i><i></i><i></i></div>
  </div>
  <div class="fcol" style="left:827px;width:200px">
    <h5>Find Us</h5>
    <p style="margin-top:18px">Lorem ipsum dolor sit amet, consectetur adipiscing elit, sed do eiusmod tempor incididunt</p>
    <div class="social"><i></i><i></i><i></i><i></i><i></i><i></i><i></i></div>
    <h5 style="margin-bottom:12px">Find Us</h5>
    <div class="contact"><svg width="12" height="12"><path d="M6 1a4 4 0 0 0-4 4c0 3 4 7 4 7s4-4 4-7a4 4 0 0 0-4-4z" fill="#1aa0f0"/></svg>Larkfield Row 42 | Brisbane</div>
    <div class="contact"><svg width="12" height="12"><path d="M2 1h3l1 3-2 1a7 7 0 0 0 3 3l1-2 3 1v3a1 1 0 0 1-1 1A10 10 0 0 1 1 2a1 1 0 0 1 1-1z" fill="#1aa0f0"/></svg>+61 7 5550 1842</div>
    <div class="contact"><svg width="12" height="12"><rect x="1" y="3" width="10" height="7" fill="#1aa0f0"/></svg>hello@marrowind.example</div>
  </div>
  <div class="bottom-bar">© 2016 COMPANY NAME | ALL RIGHTS RESERVED</div>
</footer>

</body>
</html>
```